Business Card Design Project

Looking for a logo and business card for a Real State Business i will be opening. The name is not choosen yet , but will probably be RWT IMOVEIS.
I was thinking black and silver colors, but am open to nice ideas.
I did add a business card that i liked a lot, am looking for something like that, with logo in black or silver in a black card. The logo i was thinking in the letters RWT as i uploaded or something or little and cute buildings or a house...just ideas, can be any nice logo.
Updates

You guys can add other colors if you want, I like colors very "BRIGHT" and "open", like red, pink, strong colors. almost glow in the dark colors. lol

Designers,

I've increased more 88 dollars in the budget for 1st place cause I will want envelope designs... small and big sizes.

So 1st place is now U$248,00. 

No need to send the envelope designs right now... only the business cards designs.

Thank you.

Industry/Entity Type

Business

Requirements
Must have
• Marcela Tavares Rocha

www.RWTimoveis-exemplo.com.br

+554187316042

marcela@rwtimoveis-exemplo.com.br

```html
<!DOCTYPE html>
<html lang="pt-BR">
<head>
<meta charset="utf-8">
<title>RWT Imoveis – Business Card</title>
<link rel="stylesheet" href="https://fonts.googleapis.com/css2?family=Questrial&display=swap">
<style>
  :root {
    --backdrop: #e9e4dd;
    --card: #050505;
    --accent-blue: #1e9be0;
    --silver: #d6d6d6;
    --text-light: #e6e6e6;
    --text-muted: #bdbdbd;
  }
  * { margin: 0; padding: 0; box-sizing: border-box; }
  html, body {
    width: 1200px;
    height: 900px;
    overflow: hidden;
    background: var(--backdrop);
    font-family: "Questrial", "Century Gothic", sans-serif;
  }
  .sheet {
    position: relative;
    width: 1200px;
    height: 900px;
  }
  .card {
    position: absolute;
    left: 290px;
    width: 620px;
    height: 356px;
    background: var(--card);
    box-shadow: 0 10px 28px rgba(0,0,0,0.28);
    overflow: hidden;
  }
  .card--front { top: 70px; }
  .card--back  { top: 474px; }

  .rule {
    position: absolute;
    height: 2px;
  }
  .rule--blue {
    background: linear-gradient(90deg, rgba(30,155,224,0) 0%, var(--accent-blue) 35%, var(--accent-blue) 75%, rgba(30,155,224,0) 100%);
  }
  .rule--name-top    { left: 48px; top: 92px;  width: 230px; }
  .rule--name-bottom { left: 58px; top: 150px; width: 235px; }
  .rule--silver {
    left: 80px; top: 268px; width: 520px;
    background: linear-gradient(90deg, rgba(214,214,214,0) 0%, rgba(214,214,214,0.5) 40%, var(--silver) 85%, rgba(214,214,214,0.2) 100%);
  }

  .holder {
    position: absolute;
    left: 58px;
    top: 104px;
    width: 220px;
    text-align: center;
  }
  .holder__name {
    font-size: 18px;
    color: var(--text-light);
    letter-spacing: 0.3px;
  }
  .holder__role {
    font-size: 11px;
    color: var(--text-muted);
    margin-top: 2px;
  }

  .contacts {
    position: absolute;
    left: 118px;
    top: 190px;
    list-style: none;
  }
  .contacts__item {
    display: flex;
    align-items: center;
    gap: 9px;
    font-size: 13px;
    color: var(--text-light);
    line-height: 24px;
  }
  .contacts__icon { width: 13px; height: 13px; flex: none; }

  .brand {
    position: absolute;
    left: 382px;
    top: 92px;
    display: flex;
    align-items: center;
    gap: 10px;
  }
  .brand__mark {
    width: 14px;
    height: 14px;
    background: var(--silver);
  }
  .brand__name {
    font-size: 28px;
    color: var(--silver);
    letter-spacing: 1px;
  }

  .website {
    position: absolute;
    left: 382px;
    top: 240px;
    font-size: 14px;
    color: var(--text-light);
  }
</style>
</head>
<body>
<main class="sheet">
  <section class="card card--front" aria-label="Card front">
    <span class="rule rule--blue rule--name-top"></span>
    <div class="holder">
      <p class="holder__name">Marcela Tavares Rocha</p>
      <p class="holder__role">CEO</p>
    </div>
    <span class="rule rule--blue rule--name-bottom"></span>

    <ul class="contacts">
      <li class="contacts__item">
        <svg class="contacts__icon" viewBox="0 0 13 13" aria-hidden="true">
          <rect x="3.5" y="0.5" width="6" height="12" rx="1.2" fill="none" stroke="#1e9be0" stroke-width="1.2"/>
          <rect x="5" y="2.5" width="3" height="5" fill="#1e9be0"/>
          <circle cx="6.5" cy="10.2" r="0.8" fill="#1e9be0"/>
        </svg>
        <span>554 187 316 042</span>
      </li>
      <li class="contacts__item">
        <svg class="contacts__icon" viewBox="0 0 13 13" aria-hidden="true">
          <rect x="0.6" y="2.6" width="11.8" height="8" fill="none" stroke="#1e9be0" stroke-width="1.2"/>
          <path d="M0.8 3 L6.5 7.3 L12.2 3" fill="none" stroke="#1e9be0" stroke-width="1.2"/>
        </svg>
        <span>marcela@rwtimoveis-exemplo.com.br</span>
      </li>
    </ul>

    <span class="rule rule--silver"></span>

    <div class="brand">
      <span class="brand__mark"></span>
      <span class="brand__name">RWT IMOVEIS</span>
    </div>
  </section>

  <section class="card card--back" aria-label="Card back">
    <p class="website">www.RWTimoveis-exemplo.com.br</p>
  </section>
</main>
</body>
</html>
```